Clear Plastic Card Design

I am looking to have a business card designed from my logo icon. I am looking to match the style of a different business card I have attached in the files.
Looking for a card that is plastic, with layers of transparency in the shape of my logo icon (also attached in the files) - not a circle like the other card. The winning design will incorporate the red icon logo on the front and back and include the charity's name, "Light for the Weary Souls" in the same or similar font, as well as an email and phone number. For now, use the email: email@lightfortheweary-mail.org and the phone number 555-382-7194.
We like how the sample business card has transparency, partial and full opacity layers and a matching color scheme. Files will need to be in vector so that our business card printing company can work with it.
UPDATE:
We've some excellent designs in, thank you everyone! I got an early review from the owner, and he requested a minor redirect to find his perfect design. He wants the design to stand out by NOT being a rectangle. Try instead a circle, square, or best yet - something that falls in the outline of the logo icon, either fully or partially. Thank you, everyone!
Light for the Weary Souls text should be incorporated as well as a phone and email.

```html
<!DOCTYPE html>
<html lang="en">
<head>
<meta charset="utf-8">
<title>Light for the Weary Souls – Clear Business Card</title>
<link href="https://fonts.googleapis.com/css2?family=Questrial&family=Arimo:wght@400&display=swap" rel="stylesheet">
<style>
  :root {
    --page-top: #e4ddd3;
    --page-bottom: #d3c8bb;
    --glass: rgba(255, 255, 255, 0.38);
    --glass-edge: rgba(255, 255, 255, 0.75);
    --frost: rgba(255, 255, 255, 0.22);
    --tint: rgba(212, 69, 43, 0.10);
    --band-top: #c9473a;
    --band-mid: #c02a44;
    --band-bottom: #9e1828;
    --band-right-top: #cc4f2c;
    --band-right-bottom: #b3231f;
    --accent: #d4452b;
    --ink: #2f2b2a;
    --divider: rgba(60, 55, 52, 0.6);
  }
  * { margin: 0; padding: 0; box-sizing: border-box; }
  html, body {
    width: 1200px;
    height: 969px;
    overflow: hidden;
  }
  body {
    position: relative;
    background: linear-gradient(180deg, var(--page-top), var(--page-bottom));
  }
  .card {
    position: absolute;
    left: 150px;
    top: 228px;
    width: 936px;
    height: 534px;
    clip-path: polygon(0 0, calc(100% - 44px) 0, 100% 44px, 100% 100%, 44px 100%, 0 calc(100% - 44px));
    background: var(--glass);
    box-shadow: inset 0 0 0 1px var(--glass-edge);
  }
  .card__frost {
    position: absolute;
    inset: 0;
    background:
      linear-gradient(160deg, var(--frost) 0%, rgba(255,255,255,0) 45%),
      linear-gradient(0deg, var(--tint), rgba(255,255,255,0) 60%);
  }
  .card__layer {
    position: absolute;
    background: rgba(255, 255, 255, 0.28);
  }
  .card__layer--upper { left: 20px; right: 20px; top: 0; height: 180px; }
  .card__layer--lower { left: 20px; right: 20px; bottom: 0; height: 120px; background: rgba(212, 69, 43, 0.06); }
  .edge-band {
    position: absolute;
    top: 0;
    width: 20px;
    height: 100%;
    opacity: 0.92;
  }
  .edge-band--left {
    left: 0;
    background: linear-gradient(180deg, var(--band-top), var(--band-mid) 55%, var(--band-bottom));
  }
  .edge-band--right {
    right: 0;
    background: linear-gradient(180deg, var(--band-right-top), #c33a26 60%, var(--band-right-bottom));
  }
  .brand__mark {
    position: absolute;
    left: 290px;
    top: 226px;
    width: 62px;
    height: 62px;
    background: var(--accent);
    opacity: 0.9;
  }
  .brand__name {
    position: absolute;
    left: 86px;
    top: 276px;
    font-family: "Questrial", sans-serif;
    font-size: 27px;
    line-height: 28px;
    color: var(--ink);
    white-space: nowrap;
  }
  .divider {
    position: absolute;
    left: 412px;
    top: 188px;
    width: 1.5px;
    height: 156px;
    background: var(--divider);
  }
  .contacts {
    position: absolute;
    left: 452px;
    top: 224px;
    list-style: none;
  }
  .contacts__item {
    display: flex;
    align-items: center;
    height: 28px;
    font-family: "Arimo", sans-serif;
    font-size: 21.5px;
    color: var(--ink);
    white-space: nowrap;
  }
  .contacts__icon {
    width: 18px;
    height: 18px;
    margin-right: 10px;
    flex: none;
  }
</style>
</head>
<body>
  <div class="card">
    <div class="card__frost"></div>
    <div class="card__layer card__layer--upper"></div>
    <div class="card__layer card__layer--lower"></div>
    <div class="edge-band edge-band--left"></div>
    <div class="edge-band edge-band--right"></div>

    <div class="brand__mark"></div>
    <p class="brand__name">Light for the<br>Weary Souls</p>

    <div class="divider"></div>

    <ul class="contacts">
      <li class="contacts__item">
        <svg class="contacts__icon" viewBox="0 0 20 20" aria-hidden="true">
          <path fill="#d4452b" d="M4 2c1-.6 2-.4 2.6.6l1.6 2.6c.5.8.3 1.7-.4 2.2l-1 .7c.9 2 2.4 3.7 4.4 4.8l.8-1c.6-.7 1.5-.8 2.3-.3l2.5 1.7c.9.6 1 1.7.4 2.6l-.9 1.2c-.8 1-2.2 1.3-3.4.8C7.6 16.1 3.6 11.9 2 6.8 1.6 5.4 2.1 3.9 3.2 2.6z"/>
        </svg>
        555-382-7194
      </li>
      <li class="contacts__item">
        <svg class="contacts__icon" viewBox="0 0 20 20" aria-hidden="true">
          <rect x="1.5" y="5" width="17" height="11" fill="#d4452b"/>
          <path d="M2 5.5l8 6 8-6" stroke="#f4f1ec" stroke-width="1.5" fill="none"/>
        </svg>
        email@lightfortheweary-mail.org
      </li>
      <li class="contacts__item">
        <svg class="contacts__icon" viewBox="0 0 20 20" aria-hidden="true">
          <circle cx="10" cy="10" r="8.5" fill="#d4452b"/>
          <path d="M10 1.5v17M1.5 10h17M10 1.5c-3 3-3 14 0 17M10 1.5c3 3 3 14 0 17" stroke="#f4f1ec" stroke-width="1.1" fill="none"/>
        </svg>
        www.lightfortheweary-souls.org
      </li>
    </ul>
  </div>
</body>
</html>
```